Residential Remodeling Contractor needs updated business card

I need a new design for my business card.
Name of the company is Ridgefell Construction. I need a card that commands presence, strength, integrity. I have been in business for 28 years. I am a Residential Remodeling Contractor that covers all aspects of a residential remodel and build.

```html
<!DOCTYPE html>
<html lang="en">
<head>
<meta charset="utf-8">
<title>Ridgefell Construction – Business Card</title>
<link href="https://fonts.googleapis.com/css2?family=Montserrat:wght@400;600&display=swap" rel="stylesheet">
<style>
  :root {
    --backdrop: #cfcfcd;
    --card-blue: #1f3b7c;
    --deep-blue: #16295a;
    --ink-white: #ffffff;
    --soft-white: rgba(255,255,255,0.85);
  }
  * { box-sizing: border-box; margin: 0; padding: 0; }
  html, body { width: 1200px; height: 801px; overflow: hidden; }
  body {
    background: var(--backdrop);
    font-family: "Montserrat", sans-serif;
    color: var(--ink-white);
    position: relative;
  }
  .card {
    position: absolute;
    width: 540px;
    height: 309px;
    background: var(--card-blue);
    overflow: hidden;
  }
  .card--front { left: 40px; top: 246px; }
  .card--back  { left: 620px; top: 246px; }

  /* front */
  .corner-tab {
    position: absolute; top: 0; right: 34px;
    width: 34px; height: 20px; background: var(--ink-white);
  }
  .person {
    position: absolute; top: 38px; right: 48px; text-align: right;
  }
  .person__name { font-weight: 600; font-size: 21px; letter-spacing: 0.5px; }
  .person__title { font-size: 12px; margin-top: 2px; }
  .rule {
    position: absolute; height: 1px; background: var(--soft-white);
  }
  .rule--name { top: 92px; left: 150px; right: 48px; }
  .rule--contact { top: 206px; left: 40px; width: 210px; }
  .brand {
    position: absolute; top: 120px; left: 40px;
    display: flex; align-items: center; gap: 12px;
  }
  .brand__square { width: 14px; height: 14px; background: var(--ink-white); }
  .brand__name {
    font-weight: 600; font-size: 22px; line-height: 1.1;
    text-transform: uppercase; letter-spacing: 1px;
  }
  .contact {
    position: absolute; top: 216px; left: 40px;
    font-size: 12px; line-height: 1.35;
  }
  .contact__address { margin-bottom: 8px; }
  .contact__row { display: flex; align-items: center; gap: 6px; }
  .contact__row svg { width: 11px; height: 11px; flex: none; }

  /* back */
  .back-brand {
    position: absolute; top: 98px; left: 0; right: 0; text-align: center;
    font-weight: 600; font-size: 34px; line-height: 1.1;
    text-transform: uppercase; letter-spacing: 2px;
    color: var(--deep-blue);
  }
  .tagline {
    position: absolute; bottom: 46px; right: 34px;
    font-weight: 600; font-size: 12px; letter-spacing: 0.8px;
  }
</style>
</head>
<body>
  <section class="card card--front">
    <div class="corner-tab"></div>
    <div class="person">
      <div class="person__name">MARCUS DELANE</div>
      <div class="person__title">Director</div>
    </div>
    <div class="rule rule--name"></div>

    <div class="brand">
      <span class="brand__square"></span>
      <span class="brand__name">Ridgefell<br>Construction</span>
    </div>

    <div class="rule rule--contact"></div>
    <div class="contact">
      <div class="contact__address">482 Alder Street<br>Brookvale, GA 30999</div>
      <div class="contact__row">
        <svg viewBox="0 0 12 12" aria-hidden="true"><path d="M2.5 1 L4.5 1 L5.2 3.5 L4 4.4 Q5 6.8 7.6 8 L8.5 6.8 L11 7.5 L11 9.5 Q10.5 11 9 11 Q1 10 1 2.5 Q1 1 2.5 1Z" fill="#fff"/></svg>
        <span>(555) 014-2287</span>
      </div>
      <div class="contact__row">
        <svg viewBox="0 0 12 12" aria-hidden="true"><rect x="1" y="2.5" width="10" height="7" fill="none" stroke="#fff" stroke-width="1"/><path d="M1 2.5 L6 6.5 L11 2.5" fill="none" stroke="#fff" stroke-width="1"/></svg>
        <span>info@ridgefellbuild.com</span>
      </div>
      <div class="contact__row">
        <svg viewBox="0 0 12 12" aria-hidden="true"><circle cx="6" cy="6" r="5" fill="none" stroke="#fff" stroke-width="1"/><ellipse cx="6" cy="6" rx="2.2" ry="5" fill="none" stroke="#fff" stroke-width="0.8"/><path d="M1 6 H11" stroke="#fff" stroke-width="0.8"/></svg>
        <span>www.ridgefellbuild.com</span>
      </div>
    </div>
  </section>

  <section class="card card--back">
    <div class="back-brand">Ridgefell<br>Construction</div>
    <div class="tagline">I HAVE BEEN IN BUSINESS FOR 28 YEARS</div>
  </section>
</body>
</html>
```